Brindle Asset Management Vendor Recruiting Email

We need a digital flyer to email and post on Social media to attract new vendors to our website to apply to complete maintenance work on our clients homes. I have one flyer we had produced recently that we are un-happy with. It is attached.

The example given is what we do not want!! We do not want any of the pictures used from the existing one

Target Market(s)

Construction companies and handyman

Industry/Entity Type

Residential maintenance and repairs

Requirements
Must have
• Join our team as the header not become a vendor

```html
<!DOCTYPE html>
<html lang="en">
<head>
<meta charset="utf-8">
<title>Join Our Team – Brindle Asset Management</title>
<link rel="stylesheet" href="https://fonts.googleapis.com/css2?family=Great+Vibes&family=Montserrat:wght@700&family=Oswald:wght@600&family=Archivo:ital,wght@0,500;0,800;1,500&display=swap">
<style>
  :root{
    --page:#ffffff;
    --plum:#674e7d;
    --ink:#000000;
    --white:#ffffff;
    --lime:#d6e32b;
    --blue:#1b74bb;
    --tab-ink:#5b2a8c;
    --lavender:#8986c3;
    --logo-bg:#0d0b1a;
  }
  html,body{margin:0;width:1200px;height:1200px;overflow:hidden;background:var(--page);}
  .flyer{
    position:absolute;left:30px;top:90px;width:1476px;height:1322px;
    background:var(--plum);transform:scale(0.7724);transform-origin:0 0;
    font-family:"Archivo",Arial,sans-serif;color:var(--white);overflow:hidden;
  }
  .frame{
    position:absolute;left:42px;top:24px;width:1392px;height:1273px;box-sizing:border-box;
    border:2px solid var(--white);border-radius:32px;overflow:hidden;
  }
  .footer-band{position:absolute;left:0;top:1169px;width:100%;height:75px;background:var(--ink);}
  .footer-strip{position:absolute;left:0;top:1244px;width:100%;height:30px;background:var(--lavender);}

  .headline-script{
    position:absolute;left:0;width:1476px;top:40px;text-align:center;
    font-family:"Great Vibes",cursive;font-size:150px;line-height:170px;
    color:var(--white);-webkit-text-stroke:2px var(--ink);
  }
  .headline-main{
    position:absolute;left:0;width:1476px;top:176px;text-align:center;
    font-family:"Montserrat",sans-serif;font-weight:700;font-size:172px;
    line-height:172px;color:var(--ink);letter-spacing:4px;
  }
  .divider{position:absolute;left:714px;top:379px;width:3px;height:563px;background:var(--white);}

  .list{list-style:none;margin:0;padding:0;}
  .list li{position:absolute;font-weight:500;white-space:nowrap;}
  .list li::before{
    content:"";position:absolute;width:15px;height:15px;border-radius:50%;background:var(--lime);
  }
  .benefits li{left:120px;font-size:32px;line-height:42px;letter-spacing:0.6px;}
  .benefits li::before{left:-33px;top:12px;}
  .requirements-title{
    position:absolute;left:755px;top:372px;margin:0;
    font-family:"Oswald",sans-serif;font-weight:600;font-size:50px;line-height:64px;
    color:var(--lime);text-transform:uppercase;letter-spacing:0.5px;
  }
  .requirements-title .big{font-size:54px;font-style:italic;}
  .requirements li{left:798px;font-size:29px;line-height:37px;letter-spacing:0.9px;}
  .requirements li::before{left:-34px;top:12px;}

  .contact-tab{
    position:absolute;left:296px;top:964px;width:184px;height:56px;
    background:var(--white);border-radius:5px 5px 0 0;transform:rotate(-3deg);
    font-family:"Oswald",sans-serif;font-weight:600;font-size:36px;line-height:56px;
    color:var(--tab-ink);text-align:center;
  }
  .phone{
    position:absolute;left:198px;top:1010px;width:626px;height:140px;box-sizing:border-box;
    background:var(--blue);border:4px solid var(--white);border-radius:10px;
    transform:rotate(-3deg);box-shadow:3px 4px 6px rgba(0,0,0,.35);
    font-family:"Archivo",sans-serif;font-weight:800;font-size:84px;line-height:132px;
    text-align:center;color:var(--white);letter-spacing:-1px;white-space:nowrap;
  }
  .website{
    position:absolute;left:205px;top:1195px;height:75px;display:flex;align-items:center;gap:12px;
    font-style:italic;font-size:34px;color:var(--white);white-space:nowrap;
  }
  .brand-box{
    position:absolute;left:970px;top:1077px;width:338px;height:190px;background:var(--logo-bg);
    display:flex;flex-direction:column;align-items:center;justify-content:center;gap:14px;
  }
  .brand-mark{width:22px;height:22px;background:var(--white);}
  .brand-name{font-weight:800;font-size:26px;line-height:32px;color:var(--white);text-align:center;letter-spacing:1px;}
</style>
</head>
<body>
  <section class="flyer">
    <div class="frame">
      <div class="footer-band"></div>
      <div class="footer-strip"></div>
    </div>

    <div class="headline-script">Join our</div>
    <div class="headline-main">TEAM</div>

    <div class="divider"></div>

    <ul class="list benefits">
      <li style="top:408px">95% approval rating on all<br>submitted estimates.</li>
      <li style="top:535px">Guaranteed work volume.</li>
      <li style="top:620px">Material purchasing program to<br>help vendors with low capital or no<br>or bad credit.</li>
      <li style="top:790px">Weekly secure direct deposit with<br>net 30 payment terms.</li>
    </ul>

    <h2 class="requirements-title">Requirements to become a<br><span class="big">Vendor</span></h2>

    <ul class="list requirements">
      <li style="top:511px">Auto insurance</li>
      <li style="top:578px">Certificate of general liability insurance</li>
      <li style="top:645px">Workman’s Compensation or state issued<br>exemption letter</li>
      <li style="top:749px">Drive License or state issued ID card</li>
      <li style="top:817px">Coverage area</li>
      <li style="top:884px">Any speciality Licenses</li>
    </ul>

    <div class="contact-tab">CONTACT</div>
    <div class="phone">555-214-3098</div>

    <div class="website">
      <svg width="36" height="36" viewBox="0 0 36 36" fill="none" stroke="#fff" stroke-width="2.2" aria-hidden="true">
        <circle cx="18" cy="18" r="16"/>
        <ellipse cx="18" cy="18" rx="7" ry="16"/>
        <line x1="2" y1="18" x2="34" y2="18"/>
      </svg>
      <span>www.brindleassetmanagement.com</span>
    </div>

    <div class="brand-box">
      <span class="brand-mark"></span>
      <span class="brand-name">BRINDLE<br>ASSET MANAGEMENT</span>
    </div>
  </section>
</body>
</html>
```